Architectural, Engineering and Design Build

Tovandex4.com
Veteran Disabled Certified company is doing business in Architecture, Engineer and Design build - look simialr websites and come up with design follow following website
https://hollis-darnet.example/
https://www.venlorcogroup.example/
https://www.pembrisgc.example/contract-vehicles/service-disabled-veteran-owned-small-business-sdvosb/
https://www.corbelnetlink.example/about/sdvosb/

Target Market(s)

US - Defense and Federal Government

Industry/Entity Type

Colors
0054AA
0677BA
7BADD7
CADEEF
E8F1F8

Requirements
Must have
• Army, American patriotism , Buildings, construction, architecture, engineering
Nice to have
• I need to attract federal government agencies and Defense

```html
<!DOCTYPE html>
<html lang="en">
<head>
<meta charset="utf-8">
<title>Tovandex4 — Architectural, Engineering and Design Build</title>
<link rel="stylesheet" href="https://fonts.googleapis.com/css2?family=Poppins:wght@400;500;600;700;800&display=swap">
<style>
:root{
  --navy:#17206a;
  --navy-deep:#0c1445;
  --blue:#0054aa;
  --blue-mid:#0677ba;
  --sky:#7badd7;
  --cyan:#1fa3d8;
  --red:#e0141e;
  --grey-bg:#f1f1f1;
  --white:#ffffff;
  --ink:#222;
}
*{margin:0;padding:0;box-sizing:border-box}
html,body{width:1200px;height:4577px;overflow:hidden}
body{font-family:"Poppins",sans-serif;color:var(--ink);background:var(--white);position:relative}
.abs{position:absolute}

/* hero */
.hero{left:0;top:0;width:1200px;height:770px;background:linear-gradient(180deg,#1d2330 0%,#4b5563 22%,#8a6a48 55%,#6b4a2e 80%,#4a3624 100%)}
.hero-shade{left:0;top:0;width:1200px;height:770px;background:linear-gradient(180deg,rgba(0,0,0,.45) 0%,rgba(0,0,0,.1) 30%,rgba(0,0,0,.25) 100%)}
.brand{left:73px;top:62px;display:flex;align-items:center;gap:12px;color:var(--white);font-weight:700;font-size:34px;letter-spacing:1px}
.brand-dot{width:40px;height:40px;border-radius:50%;background:var(--red)}
.nav{left:433px;top:75px;display:flex;gap:0;font-weight:600;font-size:16px}
.nav a{color:var(--white);text-decoration:none;padding:8px 14px;line-height:22px}
.nav a.active{background:var(--red)}
.hero-title{left:0;top:290px;width:1200px;text-align:center;color:var(--white);font-weight:800;font-size:92px;line-height:110px;letter-spacing:1px}
.hero-sub{left:100px;top:396px;width:1000px;text-align:center;color:var(--white);font-weight:600;font-size:29px;line-height:38px}
.btn{display:flex;align-items:center;justify-content:center;font-weight:600;color:var(--white);text-decoration:none}
.btn-red{background:var(--red)}
.hero-contact{left:407px;top:497px;width:178px;height:53px;font-size:20px}
.hero-play{left:615px;top:497px;width:180px;height:53px;font-size:20px;border:2px solid var(--white);gap:6px}

/* headings */
.section-title{left:0;width:1200px;text-align:center;color:var(--navy);font-weight:700;font-size:44px;line-height:56px}

/* services */
.svc-card{top:962px;width:328px;height:433px;border:6px solid #111}
.svc-card .svc-fill{position:absolute;inset:0}
.svc-card .svc-frame{position:absolute;left:10px;top:10px;right:10px;bottom:10px;border:2px solid var(--white)}
.svc-card h3{position:absolute;left:18px;bottom:20px;color:var(--white);font-weight:700;font-size:32px;line-height:35px}
.svc-card .svc-grad{position:absolute;left:0;right:0;bottom:0;height:160px;background:linear-gradient(180deg,rgba(0,0,0,0),rgba(0,0,0,.75))}
.arrow{width:40px;height:70px}

/* welcome */
.welcome{left:0;top:1500px;width:1200px;height:658px;background:linear-gradient(120deg,#16257a 0%,#1f3a9a 45%,#14206b 75%,#2a2f8c 100%)}
.welcome-frame{left:75px;top:1563px;width:328px;height:485px;border:3px solid var(--cyan)}
.welcome-img{left:98px;top:1595px;width:577px;height:500px;background:linear-gradient(160deg,#bfc6cf 0%,#e0b49a 55%,#f58a3c 100%)}
.welcome-title{left:702px;top:1630px;color:var(--white);font-weight:700;font-size:45px;line-height:52px}
.welcome-text{left:704px;top:1752px;width:430px;color:var(--white);font-size:15px;line-height:30px}
.welcome-btn{left:704px;top:2000px;width:180px;height:50px;font-size:19px}

/* gallery */
.tile{width:324px;height:244px}
.tile span{position:absolute;left:15px;bottom:14px;color:var(--white);font-weight:600;font-size:17px}
.tile .tile-grad{position:absolute;left:0;right:0;bottom:0;height:90px;background:linear-gradient(180deg,rgba(0,0,0,0),rgba(0,0,0,.6))}
.gallery-btn{left:489px;top:2894px;width:222px;height:52px;font-size:20px}

/* certifications */
.certs{left:0;top:3041px;width:1200px;height:421px;background:var(--grey-bg)}
.certs-text{left:80px;top:3171px;width:1040px;text-align:center;font-size:15px;line-height:31px;color:#222}
.cert-badge{top:3282px;height:95px;background:#d3d8e3;border-radius:10px}

/* contact */
.contact-img{left:471px;top:3549px;width:729px;height:481px;background:linear-gradient(180deg,#3b3f6e 0%,#c56a4a 35%,#f0a25a 50%,#6b6a5a 68%,#2f4a2a 100%)}
.contact-box{left:75px;top:3613px;width:512px;height:472px;background:linear-gradient(180deg,#d8121c 0%,#8e1a4e 45%,#2b1e75 100%)}
.contact-title{left:96px;top:3650px;color:var(--white);font-weight:700;font-size:45px;line-height:56px}
.field{border:1px solid rgba(255,255,255,.8);color:var(--white);font-size:15px;padding:12px 16px}
.submit{left:96px;top:3987px;width:230px;height:49px;font-size:21px}

/* footer */
.footer{left:0;top:4178px;width:1200px;height:332px;background:linear-gradient(120deg,#0c1445 0%,#1a2766 50%,#0f1a52 100%)}
.footer-bar{left:0;top:4510px;width:1200px;height:67px;background:#111632;color:var(--white);font-size:13px;text-align:center;line-height:67px}
.footer-brand{left:95px;top:4305px;display:flex;align-items:center;gap:12px;color:var(--white);font-weight:700;font-size:34px}
.footer-head{color:var(--white);font-weight:600;font-size:21px}
.footer-links a{display:block;color:var(--white);text-decoration:none;font-size:15px;line-height:34px}
.addr{color:var(--white);font-size:15px;line-height:28px;display:flex;gap:14px}
.addr svg{flex:none;margin-top:7px}
.social{left:795px;top:4436px;display:flex;gap:14px}
.social span{width:26px;height:26px;border-radius:50%;background:var(--white)}
</style>
</head>
<body>

<!-- Hero -->
<section class="hero abs" role="img" aria-label="Timber house framing under construction against a cloudy sky"></section>
<div class="hero-shade abs"></div>
<div class="brand abs"><span class="brand-dot"></span>TOVANDEX4</div>
<nav class="nav abs">
  <a class="active" href="#">Home</a><a href="#">About Us</a><a href="#">Services</a><a href="#">Projects</a><a href="#">Career</a><a href="#">Blog</a><a href="#">Contact Us</a>
</nav>
<h1 class="hero-title abs">TOVANDEX4</h1>
<p class="hero-sub abs">Sed ut perspiciatis unde omnis iste natus error sit voluptatem accusantium doloremque.</p>
<a class="btn btn-red hero-contact abs" href="#">Contact Us</a>
<a class="btn hero-play abs" href="#"><svg width="20" height="20" viewBox="0 0 20 20"><circle cx="10" cy="10" r="8.5" fill="none" stroke="#fff" stroke-width="2"/><path d="M8 6l6 4-6 4z" fill="#fff"/></svg>Play Video</a>

<!-- Services -->
<h2 class="section-title abs" style="top:852px">Our Services</h2>
<svg class="arrow abs" style="left:24px;top:1143px" viewBox="0 0 40 70"><path d="M32 4L6 35l26 31" fill="none" stroke="#666" stroke-width="4"/></svg>
<svg class="arrow abs" style="left:1138px;top:1143px" viewBox="0 0 40 70"><path d="M8 4l26 31L8 66" fill="none" stroke="#666" stroke-width="4"/></svg>
<div class="svc-card abs" style="left:75px">
  <div class="svc-fill" role="img" aria-label="Hands sketching architectural plans on paper" style="background:linear-gradient(160deg,#e8e4df,#b9b2aa)"></div>
  <div class="svc-grad"></div><div class="svc-frame"></div><h3>Architectural<br>Service</h3>
</div>
<div class="svc-card abs" style="left:438px">
  <div class="svc-fill" role="img" aria-label="Engineers in hard hats reviewing a blueprint on site" style="background:linear-gradient(160deg,#dfe4ea,#d98c4a 70%,#8a6a55)"></div>
  <div class="svc-grad"></div><div class="svc-frame"></div><h3>Engineering<br>Service</h3>
</div>
<div class="svc-card abs" style="left:799px">
  <div class="svc-fill" role="img" aria-label="Tower crane over a rising concrete building" style="background:linear-gradient(180deg,#3f8fe0,#7badd7 50%,#8a7a55)"></div>
  <div class="svc-grad"></div><div class="svc-frame"></div><h3>Design Build<br>Service</h3>
</div>

<!-- Welcome -->
<section class="welcome abs"></section>
<div class="welcome-frame abs"></div>
<div class="welcome-img abs" role="img" aria-label="Construction team in safety vests and white hard hats reviewing documents"></div>
<h2 class="welcome-title abs">Welcom to<br>Tovandex 4</h2>
<p class="welcome-text abs">Sed ut perspiciatis unde omnis iste natus error sit voluptatem accusantium doloremque laudantium, totam rem aperiam, eaque ipsa quae ab illo inventore veritatis et quasi architecto beatae vitae dicta sunt explicabo. Nemo enim ipsam voluptatem quia voluptas sit aspernatur aut odit aut fugit, sed quia consequuntur magni dolores eos.</p>
<a class="btn btn-red welcome-btn abs" href="#">Read More</a>

<!-- Gallery -->
<h2 class="section-title abs" style="top:2228px">Our Project Gallery</h2>
<div class="tile abs" style="left:89px;top:2334px" role="img" aria-label="Wrapped timber apartment building"><div style="position:absolute;inset:0;background:linear-gradient(180deg,#3a6fb8,#c9ccd2)"></div><div class="tile-grad"></div><span>Project 1</span></div>
<div class="tile abs" style="left:440px;top:2334px" role="img" aria-label="Scaffolded building with workers"><div style="position:absolute;inset:0;background:linear-gradient(180deg,#b7b2a6,#6e6456)"></div><div class="tile-grad"></div><span>Project 2</span></div>
<div class="tile abs" style="left:791px;top:2334px" role="img" aria-label="Large building frame at sunset"><div style="position:absolute;inset:0;background:linear-gradient(180deg,#5a7ea8,#b08a5e)"></div><div class="tile-grad"></div><span>Project 3</span></div>
<div class="tile abs" style="left:89px;top:2604px" role="img" aria-label="Steel frame house at dusk"><div style="position:absolute;inset:0;background:linear-gradient(180deg,#c9b79a,#6a5c52)"></div><div class="tile-grad"></div><span>Project 4</span></div>
<div class="tile abs" style="left:440px;top:2604px" role="img" aria-label="Concrete block building with crane"><div style="position:absolute;inset:0;background:linear-gradient(180deg,#6fa6dc,#7a7a72)"></div><div class="tile-grad"></div><span>Project 5</span></div>
<div class="tile abs" style="left:791px;top:2604px" role="img" aria-label="Timber roof framing on a house"><div style="position:absolute;inset:0;background:linear-gradient(180deg,#8fb0d4,#b67a48)"></div><div class="tile-grad"></div><span>Project 6</span></div>
<a class="btn btn-red gallery-btn abs" href="#">View All Project</a>

<!-- Certifications -->
<section class="certs abs"></section>
<h2 class="section-title abs" style="top:3107px">Key Industry Certifications</h2>
<p class="certs-text abs">Sed ut perspiciatis unde omnis iste natus error sit voluptatem accusantium doloremque laudantium, totam rem aperiam, eaque ipsa quae ab illo inventore veritatis et quasi architecto beatae vitae dicta sunt explicabo.</p>
<svg class="abs" style="left:74px;top:3312px" width="18" height="34" viewBox="0 0 18 34"><path d="M15 2L3 17l12 15" fill="none" stroke="#888" stroke-width="2.5"/></svg>
<svg class="abs" style="left:1108px;top:3312px" width="18" height="34" viewBox="0 0 18 34"><path d="M3 2l12 15L3 32" fill="none" stroke="#888" stroke-width="2.5"/></svg>
<div class="cert-badge abs" style="left:122px;width:120px"></div>
<div class="cert-badge abs" style="left:290px;width:200px"></div>
<div class="cert-badge abs" style="left:545px;width:215px"></div>
<div class="cert-badge abs" style="left:818px;width:96px"></div>
<div class="cert-badge abs" style="left:975px;width:102px;border-radius:50%"></div>

<!-- Contact -->
<div class="contact-img abs" role="img" aria-label="City skyline and park at sunset with mountains behind"></div>
<div class="contact-box abs"></div>
<h2 class="contact-title abs">Contact Us</h2>
<div class="field abs" style="left:96px;top:3728px;width:230px;height:48px">Name</div>
<div class="field abs" style="left:338px;top:3728px;width:230px;height:48px">Email Address</div>
<div class="field abs" style="left:96px;top:3795px;width:230px;height:48px">Phone No</div>
<div class="field abs" style="left:338px;top:3795px;width:230px;height:48px">Subject</div>
<div class="field abs" style="left:96px;top:3858px;width:472px;height:115px">Message</div>
<a class="btn btn-red submit abs" href="#">Submit</a>

<!-- Footer -->
<footer class="footer abs"></footer>
<div class="footer-brand abs"><span class="brand-dot"></span>TOVANDEX4</div>
<div class="footer-head abs" style="left:415px;top:4234px">Quick Link</div>
<div class="footer-links abs" style="left:415px;top:4270px"><a href="#">Home</a><a href="#">About Us</a><a href="#">Services</a><a href="#">Projects</a></div>
<div class="footer-links abs" style="left:578px;top:4270px"><a href="#">Career</a><a href="#">Blog</a><a href="#">Contact Us</a></div>
<div class="footer-head abs" style="left:795px;top:4234px">Address</div>
<div class="addr abs" style="left:795px;top:4274px;width:250px"><svg width="16" height="14" viewBox="0 0 16 14"><path d="M1 2l4-1 6 2 4-1v11l-4 1-6-2-4 1z" fill="#fff"/></svg><span>Sed ut perspiciatis unde is iste natus error</span></div>
<div class="addr abs" style="left:795px;top:4340px"><svg width="16" height="14" viewBox="0 0 16 16"><path d="M3 1l3 3-2 2a9 9 0 006 6l2-2 3 3-2 2C7 15 1 9 1 3z" fill="#fff"/></svg><span>1-888-888-8888</span></div>
<div class="addr abs" style="left:795px;top:4378px"><svg width="16" height="12" viewBox="0 0 16 12"><rect x="0" y="0" width="16" height="12" fill="#fff"/><path d="M0 0l8 6 8-6" fill="none" stroke="#1a2766" stroke-width="1.5"/></svg><span>info@companyname.com</span></div>
<div class="social abs"><span></span><span></span><span></span><span></span><span></span></div>
<div class="footer-bar abs">©2024 by Company Name. All Right Reserved</div>

</body>
</html>
```